Brightwave Reach - Business Card

We need a business card for a Social Media Marketing company that specializes in online marketing for small businesses in Canada using common Social Media platforms such as Pixlora, Chatterly, Blinkpost & Quibber.

I have uploaded a copy of our logo which I would like utilized in the business card. We would like the business card to be modern yet classy design.

Our website is www.brightwavereach.ca

Industry/Entity Type

Marketing

Contact Information for Business Card

Email: info@brightwavereach.ca
Website: www.brightwavereach.ca
Telephone: 604-555-0193

Colors

Designer to choose colors to be used in the design.

Requirements
Must have
• Social Media icons on reverse
• Please add some designs with color.

```html
<!DOCTYPE html>
<html lang="en">
<head>
<meta charset="utf-8">
<title>Brightwave Reach – Business Card</title>
<link rel="stylesheet" href="https://fonts.googleapis.com/css2?family=Roboto:wght@300;400;700;900&display=swap">
<style>
  :root {
    --backdrop: #e4e2df;
    --card-black: #000000;
    --panel-grey: #3f4447;
    --bevel-grey: #646a6e;
    --bevel-dark: #2c3032;
    --ink-white: #ffffff;
    --ink-soft: #c9cdd0;
    --accent-blue: #2f6fd6;
    --accent-pink: #d8407a;
    --accent-sky: #3fa6e8;
    --font-main: "Roboto", Helvetica, Arial, sans-serif;
  }
  * { box-sizing: border-box; margin: 0; padding: 0; }
  html, body { width: 1200px; height: 1200px; overflow: hidden; }
  body {
    background: var(--backdrop);
    font-family: var(--font-main);
    position: relative;
  }
  .card {
    position: absolute;
    left: 150px;
    width: 900px;
    height: 514px;
    background: var(--card-black);
    overflow: hidden;
    box-shadow: 0 10px 30px rgba(0,0,0,0.18);
  }
  .card--front { top: 60px; }
  .card--back { top: 626px; }

  /* front */
  .front-frame {
    position: absolute;
    inset: 34px;
    border: 3px solid var(--ink-white);
  }
  .wordmark {
    color: var(--ink-white);
    font-family: var(--font-main);
    font-weight: 900;
    text-transform: uppercase;
    text-align: center;
    line-height: 0.95;
    letter-spacing: 1px;
  }
  .card--front .wordmark {
    position: absolute;
    left: 0; right: 0; top: 50%;
    transform: translateY(-50%);
    font-size: 78px;
  }

  /* back */
  .card--back .wordmark {
    position: absolute;
    left: 40px; width: 400px;
    top: 215px;
    font-size: 50px;
  }
  .info-panel {
    position: absolute;
    left: 470px; top: 0;
    width: 390px; height: 380px;
    background: var(--panel-grey);
    border-right: 8px solid var(--bevel-dark);
  }
  .info-panel__bevel {
    position: absolute;
    left: 0; top: 0; width: 100%; height: 22px;
    background: var(--bevel-grey);
    clip-path: polygon(0 0, 100% 0, 96% 100%, 4% 100%);
  }
  .person {
    position: absolute;
    left: 44px; top: 60px;
    color: var(--ink-white);
  }
  .person__name { font-size: 56px; line-height: 1; white-space: nowrap; }
  .person__first { font-weight: 700; }
  .person__last { font-weight: 300; }
  .person__role { font-size: 24px; margin-top: 6px; }
  .person__role-light { font-weight: 300; color: var(--ink-soft); }
  .person__role-bold { font-weight: 700; }

  .contact-list {
    position: absolute;
    left: 44px; top: 212px;
    list-style: none;
  }
  .contact-list__item {
    display: flex; align-items: center;
    color: var(--ink-white);
    font-size: 19px;
    font-weight: 400;
    height: 42px;
    white-space: nowrap;
  }
  .contact-list__icon {
    width: 30px; height: 30px;
    margin-right: 14px;
    flex: none;
  }

  .social-row {
    position: absolute;
    left: 40px; right: 40px; bottom: 36px;
    display: flex; justify-content: space-between;
    list-style: none;
  }
  .social-row__item {
    display: flex; align-items: center;
    color: var(--ink-white);
    font-size: 14px;
    white-space: nowrap;
    flex: none;
  }
  .social-row__dot {
    width: 22px; height: 22px; border-radius: 50%;
    margin-right: 8px;
    flex: none;
  }
  .social-row__network { font-weight: 700; margin-right: 6px; }
  .social-row__handle { font-weight: 300; color: var(--ink-soft); }
  .dot--blue { background: var(--accent-blue); }
  .dot--pink { background: var(--accent-pink); }
  .dot--sky { background: var(--accent-sky); }
</style>
</head>
<body>

<section class="card card--front" aria-label="Business card front">
  <div class="front-frame"></div>
  <div class="wordmark">Brightwave<br>Reach</div>
</section>

<section class="card card--back" aria-label="Business card back">
  <div class="wordmark">Brightwave<br>Reach</div>

  <div class="info-panel">
    <div class="info-panel__bevel"></div>
    <div class="person">
      <div class="person__name"><span class="person__first">Jordan</span> <span class="person__last">Vale</span></div>
      <div class="person__role"><span class="person__role-light">Graphic</span> <span class="person__role-bold">Designer</span></div>
    </div>
    <ul class="contact-list">
      <li class="contact-list__item">
        <svg class="contact-list__icon" viewBox="0 0 30 30" aria-hidden="true">
          <circle cx="15" cy="15" r="14" fill="#fff"/>
          <path d="M10 8 L13 8 L14 12 L12 13.5 Q13.5 17 16.5 18 L18 16 L22 17 L22 20 Q21 22 18.5 22 Q10 20 8 11.5 Q8 9 10 8 Z" fill="#3f4447"/>
        </svg>
        604-555-0193
      </li>
      <li class="contact-list__item">
        <svg class="contact-list__icon" viewBox="0 0 30 30" aria-hidden="true">
          <circle cx="15" cy="15" r="14" fill="#fff"/>
          <rect x="8" y="10" width="14" height="10" fill="none" stroke="#3f4447" stroke-width="1.8"/>
          <path d="M8 10 L15 16 L22 10" fill="none" stroke="#3f4447" stroke-width="1.8"/>
        </svg>
        info@brightwavereach.ca
      </li>
      <li class="contact-list__item">
        <svg class="contact-list__icon" viewBox="0 0 30 30" aria-hidden="true">
          <circle cx="15" cy="15" r="14" fill="#fff"/>
          <circle cx="15" cy="15" r="8" fill="none" stroke="#3f4447" stroke-width="1.6"/>
          <ellipse cx="15" cy="15" rx="3.5" ry="8" fill="none" stroke="#3f4447" stroke-width="1.4"/>
          <path d="M7 15 H23 M8.5 11 H21.5 M8.5 19 H21.5" stroke="#3f4447" stroke-width="1.4"/>
        </svg>
        www.brightwavereach.ca
      </li>
    </ul>
  </div>

  <ul class="social-row">
    <li class="social-row__item"><span class="social-row__dot dot--blue"></span><span class="social-row__network">Chatterly</span><span class="social-row__handle">brightwavereach</span></li>
    <li class="social-row__item"><span class="social-row__dot dot--pink"></span><span class="social-row__network">Pixlora</span><span class="social-row__handle">brightwavereach</span></li>
    <li class="social-row__item"><span class="social-row__dot dot--sky"></span><span class="social-row__network">Quibber</span><span class="social-row__handle">brightwavereach</span></li>
  </ul>
</section>

</body>
</html>
```